Ward Compass Business Card Design*

We need a business card design for our company Ward Compass. Our company is specialized in providing online consulting services regarding medical institutions, hospitals and doctors. We work with patients worldwide looking to choose between healthcare providers. We have a website you may use as a reference, where we list doctors and clinics worldwide. So we target Medical providers as well as patients worldwide.
Target Market(s)
Medical Providers and patients around the world
Industry/Entity Type
Medical
Contact Information for Business Card
Salwa Kettani
CEO
+90 612 348 2175
info@wardcompass.example
www.wardcompass.example
14 Annakhil 7 H.R.B. Rabat, Morocco
Requirements
Must have
- Company logo/name on one full side, personal info and smaller logo and company name on the other side.
Nice to have
- Smart and elegant design

```html
<!DOCTYPE html>
<html lang="en">
<head>
<meta charset="utf-8">
<title>Ward Compass Business Card</title>
<link href="https://fonts.googleapis.com/css2?family=Montserrat:wght@300;400;600&display=swap" rel="stylesheet">
<style>
  :root {
    --stage: #3a3a3a;
    --card-white: #ffffff;
    --card-blue: #2fa6dc;
    --card-blue-deep: #2a95d2;
    --accent-blue: #2d9bd8;
    --navy: #1f3f7a;
    --text-gray: #4a4a4a;
    --light-gray: #6b6b6b;
  }
  * { box-sizing: border-box; margin: 0; padding: 0; }
  html, body {
    width: 1200px; height: 900px; overflow: hidden;
    background: var(--stage);
    font-family: "Montserrat", sans-serif;
  }
  .stage {
    width: 1200px; height: 900px;
    display: flex; flex-direction: column;
    align-items: center; justify-content: center; gap: 50px;
  }
  .card {
    width: 630px; height: 360px;
    border-radius: 22px;
    position: relative;
    box-shadow: 0 10px 30px rgba(0,0,0,0.35);
  }
  /* Front: personal details */
  .card--front { background: var(--card-white); }
  .person { position: absolute; left: 52px; top: 52px; }
  .person__name {
    font-size: 26px; letter-spacing: 0.5px; line-height: 1.1;
    text-transform: uppercase;
  }
  .person__first { font-weight: 600; color: var(--accent-blue); }
  .person__last { font-weight: 300; color: var(--text-gray); }
  .person__role {
    margin-top: 6px; font-size: 15px; font-weight: 400; color: var(--light-gray);
  }
  .person__rule {
    width: 54px; height: 2px; background: var(--accent-blue);
    margin: 14px 0 16px;
  }
  .contact { list-style: none; }
  .contact__item {
    display: flex; align-items: center; gap: 12px;
    font-size: 15px; font-weight: 400; color: var(--text-gray);
    margin-bottom: 8px;
  }
  .contact__icon { width: 14px; height: 14px; flex: none; }
  .front-mark {
    position: absolute; right: 50px; bottom: 46px;
    display: flex; align-items: center; gap: 10px;
  }
  .front-mark__dot {
    width: 22px; height: 22px; border-radius: 50%; background: var(--navy);
  }
  .front-mark__name {
    font-size: 22px; font-weight: 600; color: var(--navy);
    text-transform: uppercase; letter-spacing: 1px;
  }
  /* Back: company side */
  .card--back {
    background: linear-gradient(135deg, var(--card-blue) 0%, var(--card-blue-deep) 100%);
    display: flex; align-items: center; justify-content: center;
  }
  .brand { display: flex; align-items: center; gap: 16px; }
  .brand__dot {
    width: 40px; height: 40px; border-radius: 50%; background: var(--card-white);
  }
  .brand__name {
    font-size: 38px; font-weight: 400; color: var(--card-white);
    text-transform: uppercase; letter-spacing: 2px;
  }
</style>
</head>
<body>
<main class="stage">
  <section class="card card--front" aria-label="Card front with contact details">
    <div class="person">
      <h1 class="person__name"><span class="person__first">Salwa</span> <span class="person__last">Kettani</span></h1>
      <p class="person__role">CEO of Ward Compass</p>
      <div class="person__rule"></div>
      <ul class="contact">
        <li class="contact__item">
          <svg class="contact__icon" viewBox="0 0 24 24"><path fill="#2d9bd8" d="M6.6 10.8a15 15 0 0 0 6.6 6.6l2.2-2.2c.3-.3.7-.4 1-.2 1.1.4 2.3.6 3.6.6.6 0 1 .4 1 1V20c0 .6-.4 1-1 1A17 17 0 0 1 3 4c0-.6.4-1 1-1h3.5c.6 0 1 .4 1 1 0 1.3.2 2.5.6 3.6.1.3 0 .7-.2 1z"/></svg>
          +90 612 348 2175
        </li>
        <li class="contact__item">
          <svg class="contact__icon" viewBox="0 0 24 24"><rect x="2" y="5" width="20" height="14" rx="1.5" fill="#2d9bd8"/><path d="M2.5 6l9.5 7 9.5-7" fill="none" stroke="#fff" stroke-width="1.8"/></svg>
          info@wardcompass.example
        </li>
        <li class="contact__item">
          <svg class="contact__icon" viewBox="0 0 24 24"><g fill="none" stroke="#2d9bd8" stroke-width="2"><circle cx="12" cy="12" r="9.5"/><ellipse cx="12" cy="12" rx="4.5" ry="9.5"/><path d="M2.5 12h19M4 7h16M4 17h16"/></g></svg>
          www.wardcompass.example
        </li>
      </ul>
    </div>
    <div class="front-mark">
      <span class="front-mark__dot"></span>
      <span class="front-mark__name">Ward Compass</span>
    </div>
  </section>

  <section class="card card--back" aria-label="Card back with company name">
    <div class="brand">
      <span class="brand__dot"></span>
      <span class="brand__name">Ward Compass</span>
    </div>
  </section>
</main>
</body>
</html>
```